skincare creams for tired moms

I need a package and a logo design for a skincare company based in California called Petal Ledger. I make day and night cream, under eye cream, and body lotion. The first product I plan to launch is an under eye cream. It does not have to be in these colors but I do teals, greens, black, and cobalt blue.

The package is going to either be in a box or a bag. Either way I go it will be like a gift box or bag. The design should make the person feel like they are getting something special and luxurious just for them.
Updates

I have small kids and it is really difficult to find a chunk of time to myself to update or review.

Need extra days to review

Target Market(s)

mainly first time moms. I am making an under eye cream that does not use retinol but is still powerful enough to get rid of bags and dark circles.

Industry/Entity Type

Cosmetics

Logo Text

The package and logo should incorporate the name Petal Ledger.

Font styles to use
Decorative
Script

Colors

Designer to choose colors to be used in the design.

Requirements
Nice to have
• maybe focus more on Ledger instead of Petal. Also incorporate plants or flowers
Should not have
• not a huge fan of pink

```html
<!DOCTYPE html>
<html lang="en">
<head>
<meta charset="UTF-8">
<title>Petal Ledger – Under Eye Cream Box Front</title>
<link rel="stylesheet" href="https://fonts.googleapis.com/css2?family=Fondamento&family=Playfair+Display:wght@700&family=Jost:wght@300;400&display=swap">
<style>
  :root {
    --canvas-bg: #ececec;
    --box-black: #111212;
    --teal: #1b8a84;
    --teal-deep: #0f5f5b;
    --navy: #1f2a6b;
    --band-light: #f7f7f7;
    --band-mid: #dcdcdc;
    --ink: #141414;
    --white: #ffffff;
  }
  * { margin: 0; padding: 0; box-sizing: border-box; }
  html, body {
    width: 1200px;
    height: 1056px;
    overflow: hidden;
    background: var(--canvas-bg);
  }
  .stage {
    position: relative;
    width: 1200px;
    height: 1056px;
  }
  .box-front {
    position: absolute;
    left: 240px;
    top: 148px;
    width: 720px;
    height: 760px;
    background: var(--box-black);
    overflow: hidden;
    box-shadow: 0 18px 40px rgba(0,0,0,0.18);
  }
  .floral-pattern {
    position: absolute;
    inset: 0;
    background:
      radial-gradient(circle at 20% 12%, rgba(27,138,132,0.55) 0, rgba(27,138,132,0) 22%),
      radial-gradient(circle at 70% 16%, rgba(27,138,132,0.5) 0, rgba(27,138,132,0) 24%),
      radial-gradient(circle at 92% 6%, rgba(27,138,132,0.45) 0, rgba(27,138,132,0) 16%),
      radial-gradient(circle at 25% 88%, rgba(27,138,132,0.5) 0, rgba(27,138,132,0) 22%),
      radial-gradient(circle at 78% 90%, rgba(27,138,132,0.55) 0, rgba(27,138,132,0) 24%),
      var(--box-black);
  }
  .label-band {
    position: absolute;
    left: 0;
    top: 215px;
    width: 100%;
    height: 370px;
    background: linear-gradient(90deg, var(--band-mid) 0%, var(--band-light) 45%, var(--band-light) 60%, var(--band-mid) 100%);
  }
  .brand-dot {
    position: absolute;
    left: 50%;
    top: 215px;
    width: 66px;
    height: 66px;
    margin-left: -33px;
    margin-top: -33px;
    border-radius: 50%;
    background: var(--white);
  }
  .brand-name {
    position: absolute;
    left: 0;
    width: 100%;
    text-align: center;
  }
  .brand-name__petal {
    top: 268px;
    font-family: "Fondamento", serif;
    font-size: 70px;
    line-height: 1;
    color: var(--ink);
  }
  .brand-name__ledger {
    top: 348px;
    font-family: "Playfair Display", serif;
    font-weight: 700;
    font-size: 96px;
    line-height: 1;
    letter-spacing: 2px;
    color: var(--teal);
  }
  .product-type {
    position: absolute;
    left: 118px;
    width: 484px;
    top: 478px;
    height: 60px;
    border-top: 2px solid var(--teal);
    border-bottom: 2px solid var(--teal);
    display: flex;
    align-items: center;
    justify-content: center;
    font-family: "Jost", sans-serif;
    font-weight: 400;
    font-size: 32px;
    letter-spacing: 0.5px;
    color: var(--navy);
  }
  .net-volume {
    position: absolute;
    left: 50%;
    top: 665px;
    transform: translateX(-50%);
    padding: 4px 16px;
    border: 1.5px solid var(--teal);
    border-radius: 22px;
    background: var(--box-black);
    font-family: "Jost", sans-serif;
    font-weight: 300;
    font-size: 22px;
    color: var(--white);
    white-space: nowrap;
  }
</style>
</head>
<body>
  <main class="stage">
    <section class="box-front">
      <div class="floral-pattern" role="img" aria-label="Teal flowers and vines pattern on a black background"></div>
      <div class="label-band"></div>
      <div class="brand-dot"></div>
      <h1 class="brand-name brand-name__petal">Petal</h1>
      <p class="brand-name brand-name__ledger">LEDGER</p>
      <p class="product-type">UNDER EYE CREAM</p>
      <p class="net-volume">12ml | 0.41fl /oz</p>
    </section>
  </main>
</body>
</html>
```